Geschäftspapiere für Fliesenleger - Meisterbetrieb
Zielgruppe
Wir sind ein mittelständischer Fliesenleger - Meisterbetrieb und möchten unsere Geschäftspapiere erneuern. Unsere Kunden sind Privatkunden, Gewerbetreibende sowie Öffentliche Auftraggeber.
Aufgabenstellung
Unser Logo stellen wir Ihnen zur verfügung und soll unverändert bleiben.
Wir benötigen folgende Geschäftspapiere:
- Briefpapier DIN A4
- Notizblock Karriert DIN A4
- Visitenkarten 5,5 x 8,5 cm
- Kuvert DIN lang mit Fenster
- Kuvert DIN C4 mit Fenster
Bei der Farbe Rot handelt es sich um Verkehrsrot RAL 3020
Als Schriftart haben wir uns Helvetica Neue vorgestellt.
Wir bitten jedoch auch um Vorschläge anderer Moderner und gut lesbarer Schriftarten die für Print und Web bestens geeignet sind.
Wir wünschen uns ein Modernes und Schnörkelloses Design. Bei den Dateien habe ich Ihnen ein Stockphoto angehängt um Ihnen zu zeigen wie wir uns ein Cover oder eine Broschüre vorstellen können. Nur um Ihnen unsere Ideen / Vorstellungen näher zu bringen.

```html
<!DOCTYPE html>
<html lang="de">
<head>
<meta charset="utf-8">
<title>Notizblock kariert – Fliesen-Kernholt</title>
<link rel="stylesheet" href="https://fonts.googleapis.com/css2?family=Inter:wght@400&display=swap">
<style>
  :root {
    --traffic-red: #cc0605;
    --ink: #1d1d1b;
    --grid-minor: #6a6a6a;
    --grid-major: #1d1d1b;
    --paper: #ffffff;
    --backdrop: #f2f2f2;
  }
  * { margin: 0; padding: 0; box-sizing: border-box; }
  html, body {
    width: 1071px; height: 1200px; overflow: hidden;
    background: var(--backdrop);
    font-family: "Inter", "Helvetica Neue", Arial, sans-serif;
    color: var(--ink);
  }
  .sheet-frame {
    position: absolute; left: 132px; top: 30px;
    width: 806px; height: 1140px;
  }
  .notepad-sheet {
    position: absolute; left: 0; top: 0;
    width: 1188px; height: 1680px;
    background: var(--paper);
    transform: scale(0.6786);
    transform-origin: 0 0;
  }
  .sender-line {
    position: absolute; left: 97px; top: 162px;
    font-size: 13px; font-weight: 400; white-space: nowrap;
  }
  .sender-line span { margin-right: 18px; }
  .brand-name {
    position: absolute; right: 97px; top: 140px;
    font-size: 32px; font-weight: 400;
    color: var(--ink); white-space: nowrap;
  }
  .note-grid {
    position: absolute; left: 0; top: 0;
    width: 1188px; height: 1680px;
  }
  .claim-lettering {
    position: absolute; left: 99px; top: 1458px;
    width: 562px; height: 170px;
    background: var(--traffic-red);
  }
  .contact-block {
    position: absolute; left: 892px; top: 1462px;
    font-size: 18px; line-height: 21.6px; font-style: normal;
  }
  .contact-block .gap { height: 21.6px; }
</style>
</head>
<body>
  <div class="sheet-frame">
    <div class="notepad-sheet">
      <p class="sender-line"><span>KRWO Kernholt GmbH</span><span>Untermühlweg 37</span><span>91478 Sandheim</span></p>

      <p class="brand-name">Fliesen-Kernholt</p>

      <svg class="note-grid" viewBox="0 0 1188 1680" aria-hidden="true">
        <defs>
          <pattern id="minor-columns" patternUnits="userSpaceOnUse" x="80" y="0" width="31.2" height="10">
            <rect x="0" y="0" width="1" height="10" fill="var(--grid-minor)"/>
          </pattern>
          <pattern id="minor-rows" patternUnits="userSpaceOnUse" x="0" y="406" width="10" height="31.2">
            <rect x="0" y="0" width="10" height="1" fill="var(--grid-minor)"/>
          </pattern>
          <pattern id="major-columns" patternUnits="userSpaceOnUse" x="205" y="0" width="156" height="10">
            <rect x="0" y="0" width="1.8" height="10" fill="var(--grid-major)"/>
          </pattern>
          <pattern id="major-rows" patternUnits="userSpaceOnUse" x="0" y="406" width="10" height="156">
            <rect x="0" y="0" width="10" height="1.8" fill="var(--grid-major)"/>
          </pattern>
        </defs>
        <rect x="72" y="371" width="1044" height="1042" fill="url(#minor-columns)"/>
        <rect x="72" y="400" width="1044" height="1013" fill="url(#minor-rows)"/>
        <rect x="72" y="371" width="1044" height="1042" fill="url(#major-columns)"/>
        <rect x="72" y="400" width="1044" height="1013" fill="url(#major-rows)"/>
      </svg>

      <div class="claim-lettering" role="img" aria-label="Großer handgeschriebener Slogan in Rot"></div>

      <address class="contact-block">
        <p>KRWO Kernholt GmbH</p>
        <p>Untermühlweg 37</p>
        <p>91478 Sandheim</p>
        <div class="gap"></div>
        <p>Tel.: 09174-5512830</p>
        <p>Fax: 09174-5512839</p>
        <p>Email: post@fliesen-kernholt.de</p>
        <p>Web: www.fliesen-kernholt.de</p>
      </address>
    </div>
  </div>
</body>
</html>
```